Mobile Fitness snd Therapy Business Card Design

I need a business card designed for my mobile fitness and therapy business.

Please view the images that I have uploaded. I like the simplicity of the design that I have attached. I adapted it with my information

Target Market(s)

Those seeking personal training, injury rehabilitation or massage therapy.

Industry/Entity Type

Business

Contact Information for Business Card

Derek Fulham - MSc, CAT(C), RMT, CSCS, Pn2
e-mail: derek@vantrelo.com
website: www.vantrelo.com
instagram: @derek_fulham

Font styles to use
Sans Serif

Colors
3176b5
0355a3

Requirements
Must have
• "Contact us to receive a FREE assessment"
• Services offered:
• Personal Training
• Golf Fitness
• Injury Rehab
• Massage Therapy
• Yoga
Nice to have
• Consistent colours with brand
• - Dark Blue: #232837
• - Blue: #5096f0
• Consistent look/feel with the website: www.vantrelo.com

```html
<!DOCTYPE html>
<html lang="en">
<head>
<meta charset="utf-8">
<title>Vantrelo Business Card</title>
<link rel="stylesheet" href="https://fonts.googleapis.com/css2?family=Montserrat:wght@600&family=Roboto:wght@400;500&family=Roboto+Condensed:wght@500;700&display=swap">
<style>
  :root {
    --stage-bg: #e9e9ec;
    --card-light: #f6f6f6;
    --card-dark: #232837;
    --ink-dark: #232837;
    --ink-body: #3a3d45;
    --brand-blue: #2a5bd7;
    --accent-blue: #5096f0;
    --white: #ffffff;
    --divider: #7d8aa8;
  }
  * { box-sizing: border-box; margin: 0; padding: 0; }
  html, body { width: 1200px; height: 960px; overflow: hidden; }
  body { background: var(--stage-bg); font-family: "Roboto", sans-serif; }

  .stage { position: relative; width: 1200px; height: 960px; }

  .card {
    position: absolute;
    width: 600px;
    height: 343px;
    border-radius: 20px;
    overflow: hidden;
  }

  /* Front face */
  .card--front { left: 315px; top: 113px; background: var(--card-light); }

  .brand-name {
    font-family: "Montserrat", sans-serif;
    font-weight: 600;
    letter-spacing: 3px;
    white-space: nowrap;
  }
  .brand-tagline {
    font-family: "Montserrat", sans-serif;
    font-weight: 600;
    white-space: nowrap;
  }

  .card--front .brand-name {
    position: absolute; left: 42px; top: 36px;
    font-size: 38px; line-height: 1; color: var(--ink-dark);
  }
  .card--front .brand-tagline {
    position: absolute; left: 43px; top: 80px;
    font-size: 12.5px; letter-spacing: 2.2px; color: var(--ink-dark);
  }

  .holder { position: absolute; left: 43px; top: 190px; }
  .holder__name {
    font-family: "Roboto Condensed", sans-serif;
    font-weight: 700; font-size: 22px; line-height: 1;
    color: var(--brand-blue); text-transform: uppercase;
  }
  .holder__credentials {
    margin-top: 5px;
    font-family: "Roboto Condensed", sans-serif;
    font-weight: 700; font-size: 11px;
    color: var(--brand-blue);
  }

  .contact-list { position: absolute; left: 43px; top: 247px; list-style: none; }
  .contact-list li {
    display: flex; align-items: center; gap: 8px;
    height: 19px; font-size: 14px; color: var(--ink-body);
  }
  .contact-list svg { width: 14px; height: 14px; flex: none; }

  /* Back face */
  .card--back { left: 311px; top: 473px; background: var(--card-dark); text-align: center; }
  .card--back .brand-name {
    position: absolute; left: 0; right: 0; top: 124px;
    font-size: 46px; line-height: 1; color: var(--white);
  }
  .card--back .brand-tagline {
    position: absolute; left: 0; right: 0; top: 180px;
    font-size: 15.5px; letter-spacing: 2.6px; color: var(--white);
  }

  .offer {
    position: absolute; left: 58px; top: 257px;
    width: 484px; height: 33px; border-radius: 17px;
    background: var(--brand-blue);
    font-family: "Roboto Condensed", sans-serif;
    font-weight: 700; font-size: 20.5px; line-height: 33px;
    color: var(--white); text-transform: uppercase;
  }
  .services {
    position: absolute; left: 0; right: 0; top: 296px;
    font-size: 14.5px; color: var(--white); white-space: nowrap;
  }
  .services .sep { color: var(--divider); margin: 0 3px; }
</style>
</head>
<body>
<main class="stage">

  <section class="card card--front" aria-label="Card front">
    <div class="brand-name">VANTRELO</div>
    <div class="brand-tagline">NUTRITION - FITNESS - HEALTH</div>

    <div class="holder">
      <h1 class="holder__name">Derek Fulham</h1>
      <p class="holder__credentials">MSC, CAT(C), RMT, CSCS, PN2</p>
    </div>

    <ul class="contact-list">
      <li>
        <svg viewBox="0 0 14 14" aria-hidden="true"><rect x="1" y="3" width="12" height="8.5" rx="1" fill="#2a5bd7"/><path d="M1.5 3.6 7 7.8l5.5-4.2" fill="none" stroke="#fff" stroke-width="1.1"/></svg>
        derek@vantrelo.com
      </li>
      <li>
        <svg viewBox="0 0 14 14" aria-hidden="true"><circle cx="7" cy="7" r="6" fill="#2a5bd7"/><ellipse cx="7" cy="7" rx="2.5" ry="6" fill="none" stroke="#fff" stroke-width="0.9"/><path d="M1 7h12" stroke="#fff" stroke-width="0.9"/></svg>
        www.vantrelo.com
      </li>
      <li>
        <svg viewBox="0 0 14 14" aria-hidden="true"><circle cx="7" cy="7" r="6" fill="#2a5bd7"/></svg>
        @derek_fulham
      </li>
    </ul>
  </section>

  <section class="card card--back" aria-label="Card back">
    <div class="brand-name">VANTRELO</div>
    <div class="brand-tagline">NUTRITION - FITNESS - HEALTH</div>
    <p class="offer">Contact us to receive a free assessment</p>
    <p class="services">Personal Training<span class="sep">|</span>Golf Fitness<span class="sep">|</span>Injury Rehab<span class="sep">|</span>Massage Therapy<span class="sep">|</span>Yoga</p>
  </section>

</main>
</body>
</html>
```